Anzeigengestaltung für Verkauf & Installation von Alarmanlagen und Videoüberwachungssystemen
Zielgruppe
Verkauf und Installation von Alarmanlagen und Videoüberwachungssystemen.
Verkauf erfolgt über eigenen Onlineshop.
Installation der Anlagen im regionalen Umkreis, hauptsächlich Privatkunden.
Zielgruppe: Privatkunden, Familien, mit vorhandener Immobilie/Wohneigentum.
Aufgabenstellung
Zeitungsformat:
92 mm x 60 mm
s/w-4C
Text Entwurf als Orientierung befindet sich im Anhang, ebenso das Firmenlogo.
Bilder aus der Webseite sind ebenfalls beigefügt. Vielleicht lässt sich damit etwas anfangen, ich bin aber auch für Vorschläge aus geeigneten Stock-Bildern offen.

```html
<!DOCTYPE html>
<html lang="de">
<head>
<meta charset="utf-8">
<title>Schutzwerk Hof – Anzeige</title>
<link rel="stylesheet" href="https://fonts.googleapis.com/css2?family=Oswald:wght@500&family=Roboto:wght@400;500;700&display=swap">
<style>
  :root {
    --brand-red: #d6402b;
    --ink: #1d1d1b;
    --panel-light: #f6f6f6;
    --panel-grey: #e6e6e6;
    --page: #ffffff;
    --white: #ffffff;
  }
  html, body {
    margin: 0;
    padding: 0;
    width: 756px;
    height: 1200px;
    overflow: hidden;
    background: var(--page);
  }
  .ad {
    position: absolute;
    left: 28px;
    top: 372px;
    width: 700px;
    height: 456px;
    box-sizing: border-box;
    border: 1.5px solid var(--brand-red);
    overflow: hidden;
    background: linear-gradient(160deg, var(--panel-light) 0%, var(--panel-grey) 100%);
    font-family: "Roboto", Arial, sans-serif;
    color: var(--ink);
  }
  .ad-shapes {
    position: absolute;
    inset: 0;
  }
  .brand {
    position: absolute;
    left: 372px;
    top: 36px;
    display: flex;
    align-items: center;
    gap: 14px;
  }
  .brand-mark {
    width: 52px;
    height: 52px;
    border-radius: 50%;
    background: var(--ink);
  }
  .brand-name {
    font-family: "Roboto", Arial, sans-serif;
    font-weight: 700;
    font-size: 30px;
    line-height: 1;
    color: var(--ink);
  }
  .brand-claim {
    font-size: 9px;
    font-weight: 500;
    color: var(--ink);
    margin-top: 4px;
  }
  .headline {
    position: absolute;
    left: 384px;
    top: 138px;
    margin: 0;
    font-family: "Oswald", "Arial Narrow", sans-serif;
    font-weight: 500;
    font-size: 24px;
    letter-spacing: 0.3px;
    color: var(--ink);
  }
  .benefits {
    position: absolute;
    left: 384px;
    top: 190px;
    margin: 0;
    padding: 0;
    list-style: none;
    font-size: 18px;
    font-weight: 500;
  }
  .benefits li {
    display: flex;
    align-items: center;
    gap: 8px;
    height: 27px;
  }
  .tick { width: 16px; height: 16px; flex: none; }
  .funding-band {
    position: absolute;
    left: 371px;
    right: -2px;
    top: 294px;
    height: 44px;
    background: var(--brand-red);
    border-radius: 22px 0 0 22px;
    color: var(--white);
    font-family: "Oswald", "Arial Narrow", sans-serif;
    font-weight: 500;
    font-size: 20px;
    line-height: 44px;
    padding-left: 32px;
    white-space: nowrap;
  }
  .services {
    position: absolute;
    left: 390px;
    top: 356px;
    display: flex;
    gap: 14px;
    font-family: "Oswald", "Arial Narrow", sans-serif;
    font-weight: 500;
    font-size: 14px;
  }
  .service {
    display: flex;
    align-items: center;
    gap: 6px;
  }
  .service svg { width: 24px; height: 24px; }
  .contact {
    position: absolute;
    right: 16px;
    top: 400px;
    text-align: right;
    font-size: 11px;
    line-height: 19px;
    white-space: nowrap;
  }
  .dot { color: var(--brand-red); }
</style>
</head>
<body>
  <section class="ad">
    <svg class="ad-shapes" width="700" height="456" viewBox="0 0 700 456">
      <defs>
        <linearGradient id="scene-tone" x1="0" y1="0" x2="1" y2="1">
          <stop offset="0" stop-color="#b23a2c"/>
          <stop offset="0.35" stop-color="#e7d9a8"/>
          <stop offset="0.7" stop-color="#b9bcbf"/>
          <stop offset="1" stop-color="#d8342a"/>
        </linearGradient>
      </defs>
      <polygon points="0,0 258,0 343,191 222,456 0,456" fill="url(#scene-tone)" role="img" aria-label="Illustration: Einfamilienhaus mit Tor, Überwachungskamera, Türsprechanlage mit Tastenfeld und rote Alarmleuchte"/>
      <polyline points="266,-2 355,191 234,458" fill="none" stroke="#d6402b" stroke-width="8"/>
    </svg>

    <div class="brand">
      <div class="brand-mark"></div>
      <div>
        <div class="brand-name">Schutzwerk Hof</div>
        <div class="brand-claim">Schützen Sie sich und Ihr Eigentum</div>
      </div>
    </div>

    <h1 class="headline">MODERNE FUNKALARMANLAGEN</h1>

    <ul class="benefits">
      <li><svg class="tick" viewBox="0 0 16 16"><circle cx="8" cy="8" r="8" fill="#1d1d1b"/><path d="M4.5 8.3l2.3 2.3 4.7-4.9" fill="none" stroke="#fff" stroke-width="2"/></svg>Individuelle Beratung</li>
      <li><svg class="tick" viewBox="0 0 16 16"><circle cx="8" cy="8" r="8" fill="#1d1d1b"/><path d="M4.5 8.3l2.3 2.3 4.7-4.9" fill="none" stroke="#fff" stroke-width="2"/></svg>Onlineshop</li>
      <li><svg class="tick" viewBox="0 0 16 16"><circle cx="8" cy="8" r="8" fill="#1d1d1b"/><path d="M4.5 8.3l2.3 2.3 4.7-4.9" fill="none" stroke="#fff" stroke-width="2"/></svg>Installation</li>
    </ul>

    <div class="funding-band">HEIMBANK FÖRDERUNG MÖGLICH</div>

    <div class="services">
      <div class="service">
        <svg viewBox="0 0 24 24"><path d="M7 19v-7a5 5 0 0 1 10 0v7z" fill="#d6402b"/><rect x="5" y="19" width="14" height="3" fill="#1d1d1b"/><path d="M12 2v3M4 6l2 2M20 6l-2 2" stroke="#1d1d1b" stroke-width="1.5"/></svg>
        ALARM
      </div>
      <div class="service">
        <svg viewBox="0 0 24 24"><path d="M3 8V3h5M16 3h5v5M21 16v5h-5M8 21H3v-5" fill="none" stroke="#1d1d1b" stroke-width="2"/><circle cx="12" cy="12" r="3" fill="#d6402b"/></svg>
        VIDEO
      </div>
      <div class="service">
        <svg viewBox="0 0 24 24"><path d="M2 11l7-6 7 6" fill="none" stroke="#1d1d1b" stroke-width="2"/><rect x="4" y="11" width="9" height="9" fill="none" stroke="#1d1d1b" stroke-width="2"/><rect x="14" y="8" width="8" height="14" rx="1" fill="#1d1d1b"/><path d="M18 11l2 4h-4z" fill="#d6402b"/></svg>
        HAUSAUTOMATION
      </div>
    </div>

    <div class="contact">
      Lindenstraße 12 <span class="dot">●</span> 71234 Musterfeld <span class="dot">●</span> 01234-5678<br>
      www.schutzwerkhof.de&nbsp; E-Mail: info@schutzwerkhof.de
    </div>
  </section>
</body>
</html>
```